Brightway Haus Inc. Business Card Design

Brightway Haus Inc. is in search of a great clean design for our business cards!

Looking to incorporate our full logo and watermark on side one (however, I am open to having the text and watermark separated within the design.)

On side two, I am looking to have contact information (Name, Position, Phone #, Email, Website (www.thebrightwayhaus.ca). Can have the logo and/or watermark as part of the design if applicable.

Please add tagline "Where Shine Counts" on either side 1 or 2. This tagline can be in a sans serif, serif or cursive font as long as it compliments overall design. Capitalization can be title or sentence case depending on how it fits within the design.

Get creative!! Looking for a clean, crisp, premium design! Looking for a glossy card finish with spot UV features when printed. Cards will also be printed with rounded corners. Standard dimensions (3.5 x 2).

Target Market(s)

B2B - primary clients are business owners or property management corporations. (residential jobs are few and far between)

Industry/Entity Type

Business

Contact Information for Business Card

- clean, crisp design
- double sided
- spot UV accents and glossy finish upon printing
- standard business card size (3.5 x 2) with rounded corners
- please see project description for requirements per side

Font styles to use
Sans Serif

Requirements
Must have
• - adequate bleeds with print ready files
• - cohesive design elements between side 1 & 2
• - spot UV elements (can be on both sides or just one, use your discretion)
• - colour pallet should match the logo file provided
• - incorporate tagline "where shine counts" (this tagline can be in a serif or sans serif font as long as it is complimentary to the overall design.
Nice to have
• - Premium elements with a clean design
Should not have
• - Please omit cartoon or whimsical like designs, think premium.
• - Colours should not stray from the pallet of the provided logo.

```html
<!DOCTYPE html>
<html lang="en">
<head>
<meta charset="utf-8">
<title>Brightway Haus Inc. – Business Card</title>
<link href="https://fonts.googleapis.com/css2?family=Open+Sans:wght@700;800&family=Roboto:ital,wght@0,400;1,400&display=swap" rel="stylesheet">
<style>
  :root {
    --teal: #12b2b3;
    --navy: #1b2350;
    --paper: #f2f2f2;
    --stage: #2a2a2a;
    --ink-light: #ffffff;
    --rule: #555a6e;
  }
  * { box-sizing: border-box; margin: 0; padding: 0; }
  html, body { width: 1200px; height: 960px; overflow: hidden; }
  body { background: var(--stage); position: relative; font-family: "Roboto", sans-serif; }

  .card {
    position: absolute;
    width: 600px;
    height: 342px;
    border-radius: 22px;
    background: var(--paper);
    overflow: hidden;
  }
  .card--front { left: 314px; top: 114px; }
  .card--back  { left: 311px; top: 472px; }

  .front-panel { position: absolute; inset: 0; width: 600px; height: 342px; }

  .brand {
    position: absolute;
    display: flex;
    align-items: center;
    gap: 10px;
    font-family: "Open Sans", sans-serif;
    font-weight: 800;
    color: var(--navy);
    white-space: nowrap;
  }
  .brand__mark { background: var(--teal); flex: none; }
  .card--front .brand { left: 44px; top: 42px; font-size: 28px; letter-spacing: -0.5px; }
  .card--front .brand__mark { width: 26px; height: 26px; }

  .person { position: absolute; left: 44px; top: 114px; font-family: "Open Sans", sans-serif; font-weight: 700; }
  .person__name { color: var(--teal); font-size: 20px; line-height: 26px; }
  .person__role { color: var(--navy); font-size: 14.5px; line-height: 20px; }

  .contact {
    position: absolute;
    right: 24px;
    top: 176px;
    color: var(--ink-light);
    font-size: 14.5px;
    text-align: right;
    white-space: nowrap;
  }
  .contact__address { line-height: 19px; margin-bottom: 7px; }
  .contact__row { display: flex; justify-content: flex-end; align-items: center; gap: 7px; line-height: 19.3px; }
  .contact__icon { width: 14px; height: 14px; flex: none; fill: var(--ink-light); }

  .card--back .brand {
    left: 0; right: 0; top: 140px;
    justify-content: center;
    font-size: 40px;
    gap: 14px;
    letter-spacing: -0.5px;
  }
  .card--back .brand__mark { width: 38px; height: 38px; }

  .tagline {
    position: absolute;
    left: 0; right: 0; top: 278px;
    display: flex; align-items: center; justify-content: center; gap: 6px;
    font-style: italic;
    font-size: 19px;
    color: var(--navy);
  }
  .tagline__rule { width: 118px; height: 1px; }
  .tagline__rule--left  { background: linear-gradient(to right, transparent, var(--rule)); }
  .tagline__rule--right { background: linear-gradient(to left, transparent, var(--rule)); }
  .tagline__accent { color: var(--teal); }
</style>
</head>
<body>

<section class="card card--front" aria-label="Card front">
  <svg class="front-panel" viewBox="0 0 600 342" aria-hidden="true">
    <polygon fill="var(--navy)" points="412,0 420,0 320,342 312,342"/>
    <polygon fill="var(--teal)" points="432,0 600,0 600,342 332,342"/>
  </svg>

  <div class="brand"><span class="brand__mark"></span>Brightway Haus Inc.</div>

  <div class="person">
    <p class="person__name">DANIEL HARPER</p>
    <p class="person__role">CEO/FOUNDER</p>
  </div>

  <div class="contact">
    <p class="contact__address">4210 Alder Crest Way<br>Halton, Ontario 58201</p>
    <p class="contact__row">905 312 4470
      <svg class="contact__icon" viewBox="0 0 16 16" aria-hidden="true"><path d="M3.6 1.2l2.3 2.6-1.4 1.8c.9 2 2.5 3.6 4.5 4.5l1.8-1.4 2.6 2.3-1.3 2.6C6.7 13.3 2.7 9.3 1 3.9z"/></svg></p>
    <p class="contact__row">905 718 2261
      <svg class="contact__icon" viewBox="0 0 16 16" aria-hidden="true"><path d="M4.5 0.5h7v15h-7z M5.8 2v10.5h4.4V2z" fill-rule="evenodd"/></svg></p>
    <p class="contact__row">905 312 4471
      <svg class="contact__icon" viewBox="0 0 16 16" aria-hidden="true"><path d="M4 1h8v4H4z M1 6h14v6h-2v-2H3v2H1z M4 11h8v4H4z"/></svg></p>
    <p class="contact__row">hello@thebrightwayhaus.ca
      <svg class="contact__icon" viewBox="0 0 16 16" aria-hidden="true"><path d="M1 3.5h14v9H1z"/><path d="M2 4.5l6 4.5 6-4.5" fill="none" stroke="var(--teal)" stroke-width="1.2"/></svg></p>
    <p class="contact__row">www.thebrightwayhaus.ca
      <svg class="contact__icon" viewBox="0 0 16 16" aria-hidden="true"><circle cx="8" cy="8" r="7"/><path d="M5 4c2 1 1 3 3 3s1 3 3 3M9 2c0 2 2 2 3 2" fill="none" stroke="var(--teal)" stroke-width="1.4"/></svg></p>
  </div>
</section>

<section class="card card--back" aria-label="Card back">
  <div class="brand"><span class="brand__mark"></span>Brightway Haus Inc.</div>
  <p class="tagline">
    <span class="tagline__rule tagline__rule--left"></span>
    <span>Where <span class="tagline__accent">Shine</span> Counts</span>
    <span class="tagline__rule tagline__rule--right"></span>
  </p>
</section>

</body>
</html>
```